Local fast-growing company in the service sector

We are looking for a modern business card design, which should also appear on our letterheads

Target Market(s)

Private and industrial sectors

Contact Information for Business Card

Vorname Name
Kellberger Str. 18
72458 Brunnhof
Tel.: 07146-839214-0
Name@agentur-kvtl.de

Colors
9d9d9d
919191
aaaaaa

Requirements
Must have
• The logo (file) in silver

```html
<!DOCTYPE html>
<html lang="de">
<head>
<meta charset="utf-8">
<title>KVTL – Visitenkarte</title>
<link rel="stylesheet" href="https://fonts.googleapis.com/css2?family=Arimo:wght@400;700&display=swap">
<style>
  :root {
    --page-bg: #d4d4d4;
    --card-top: #f1f1f1;
    --card-bottom: #e2e2e2;
    --silver: #9d9d9d;
    --silver-mid: #919191;
    --silver-light: #aaaaaa;
    --brand-ink: #5e5e5e;
    --ink: #1d1d1d;
    --ink-soft: #3a3a3a;
    --rule: #8a8a8a;
    --band: #5c5c5c;
  }
  * { box-sizing: border-box; margin: 0; padding: 0; }
  html, body {
    width: 1200px; height: 970px; overflow: hidden;
    background: var(--page-bg);
    font-family: "Arimo", Arial, sans-serif;
  }
  .canvas { position: relative; width: 1200px; height: 970px; }
  .business-card {
    position: absolute; left: 100px; top: 185px;
    width: 1000px; height: 600px;
    background: linear-gradient(180deg, var(--card-top), var(--card-bottom));
    border: 1px solid #c4c4c4;
    box-shadow: 0 10px 30px rgba(0,0,0,0.12);
    overflow: hidden;
  }
  .brand {
    position: absolute; left: 0; right: 0; top: 88px;
    display: flex; justify-content: center; align-items: center; gap: 28px;
  }
  .brand-mark {
    width: 118px; height: 118px;
    background: var(--silver);
  }
  .brand-text { display: flex; flex-direction: column; }
  .brand-name {
    font-weight: 700; font-size: 100px; line-height: 0.9;
    letter-spacing: 2px; color: var(--brand-ink);
  }
  .brand-web {
    font-weight: 400; font-size: 33px; letter-spacing: 2px;
    color: var(--brand-ink); margin-top: 6px;
  }
  .person {
    position: absolute; left: 46px; right: 52px; top: 300px;
    display: flex; align-items: center; gap: 14px;
  }
  .person-rule { flex: 1; height: 2px; background: var(--rule); }
  .person-name {
    font-weight: 700; font-size: 33px; color: var(--ink); letter-spacing: 0.5px;
  }
  .person-role {
    position: absolute; left: 0; right: 0; top: 346px;
    text-align: center; font-size: 20px; letter-spacing: 1px; color: var(--ink-soft);
  }
  .contact-icons {
    position: absolute; left: 0; right: 0; top: 398px;
    display: flex; justify-content: center; gap: 20px;
  }
  .contact-icons svg { width: 32px; height: 32px; }
  .contact-lines {
    position: absolute; left: 0; right: 0; top: 458px;
    text-align: center; color: var(--ink);
    font-size: 23px; line-height: 35px; letter-spacing: 1.5px;
  }
  .contact-lines .address { letter-spacing: 0.3px; }
  .card-band {
    position: absolute; left: 0; right: 0; bottom: 0; height: 30px;
    background: linear-gradient(90deg, var(--silver-light), var(--band) 60%, #4a4a4a);
  }
</style>
</head>
<body>
<div class="canvas">
  <div class="business-card">
    <div class="brand">
      <div class="brand-mark"></div>
      <div class="brand-text">
        <span class="brand-name">KVTL</span>
        <span class="brand-web">agentur-kvtl.de</span>
      </div>
    </div>

    <div class="person">
      <span class="person-rule"></span>
      <span class="person-name">JONAS BERGER</span>
      <span class="person-rule"></span>
    </div>
    <div class="person-role">CO-FOUNDER</div>

    <div class="contact-icons">
      <svg viewBox="0 0 32 32" aria-label="Telefon / Fax">
        <circle cx="16" cy="16" r="16" fill="var(--silver-mid)"/>
        <rect x="11" y="8" width="10" height="5" fill="#fff"/>
        <rect x="8" y="13" width="16" height="8" rx="1.5" fill="#fff"/>
        <rect x="11" y="18" width="10" height="6" fill="#fff" stroke="var(--silver-mid)" stroke-width="1"/>
      </svg>
      <svg viewBox="0 0 32 32" aria-label="E-Mail">
        <circle cx="16" cy="16" r="16" fill="var(--silver-mid)"/>
        <rect x="8" y="10" width="16" height="12" fill="#fff"/>
        <path d="M8 10 L24 22 M24 10 L8 22" stroke="var(--silver-mid)" stroke-width="1.6"/>
      </svg>
      <svg viewBox="0 0 32 32" aria-label="Website">
        <circle cx="16" cy="16" r="16" fill="var(--silver-mid)"/>
        <rect x="8" y="14" width="10" height="5" rx="2.5" fill="none" stroke="#fff" stroke-width="2" transform="rotate(-45 13 16.5)"/>
        <rect x="14" y="13" width="10" height="5" rx="2.5" fill="none" stroke="#fff" stroke-width="2" transform="rotate(-45 19 15.5)"/>
      </svg>
    </div>

    <div class="contact-lines">
      <div class="phone">07146-839214-0</div>
      <div class="email">Name@agentur-kvtl.de</div>
      <div class="address">Kellberger Str. 18,72458 Brunnhof</div>
    </div>

    <div class="card-band"></div>
  </div>
</div>
</body>
</html>
```